We need our current web site completely overhauled logo and all. www.maplecrestkidsclub.com

This is a web site for a before and after school program for kids. I would like to see a fresh and cleaner version. The current version was created 8 to 10 years ago.
www.maplecrestkidsclub.com

```html
<!DOCTYPE html>
<html lang="en">
<head>
<meta charset="utf-8">
<title>Maple Crest – Before &amp; After School Program</title>
<link href="https://fonts.googleapis.com/css2?family=Ubuntu:wght@300;400;500;700&display=swap" rel="stylesheet">
<style>
:root{
  --green:#2d6b4c;
  --green-dark:#1f5a3d;
  --green-text:#2e6e4d;
  --ink:#333;
  --muted:#666;
  --line:#d8d8d8;
  --panel:#3d3d3d;
  --footer:#2b2b2b;
  --gold:#f0b400;
  --red:#b3141b;
  --yellow-band:#d8b400;
  --blue-band:#1e3f7a;
  --submit:#2fb877;
}
*{box-sizing:border-box;margin:0;padding:0}
html,body{width:890px;height:1200px;overflow:hidden}
body{position:relative;background:#fff;font-family:"Ubuntu",sans-serif;color:var(--ink)}
.abs{position:absolute}

/* header */
.brand{left:76px;top:22px;font-weight:700;font-size:30px;color:var(--green-dark);line-height:1;display:flex;align-items:center;gap:8px}
.brand-dot{width:14px;height:14px;background:var(--green);border-radius:50%}
.call{right:74px;top:20px;font-size:15px;font-weight:300;color:#666}
.call b{font-weight:400;color:var(--green-dark)}
.search{left:675px;top:47px;width:141px;height:25px;border:1px solid #c8c8c8;background:#fafafa;font-size:10px;color:#888;padding:6px 11px}
.search svg{position:absolute;right:6px;top:5px}

/* nav */
.nav{left:0;top:92px;width:890px;height:36px;background:linear-gradient(#4c8a68,#22573b);border-top:2px solid #2f6a4a;border-bottom:2px solid #9cc0a8}
.nav ul{list-style:none;display:flex;position:absolute;left:90px;top:6px}
.nav li{font-size:10.5px;font-weight:500;color:#fff;padding:5px 8px;margin-right:11px;height:24px;line-height:14px;letter-spacing:-.1px}
.nav li.active{background:#111;border-radius:2px}

/* slider */
.hero-band{left:0;top:128px;width:890px;height:283px;background:linear-gradient(#dcdcdc,#f2f2f2 60%,#fafafa);border-bottom:1px solid var(--line)}
.hero-frame{left:74px;top:141px;width:742px;height:259px;background:#fff;border:1px solid #e2e2e2;border-radius:3px}
.hero-photo{left:81px;top:148px;width:728px;height:245px;border-radius:2px;background:linear-gradient(90deg,#5d6a55 0%,#9a8e72 30%,#c9c3b5 55%,#ececec 75%,#f2f2f2 100%)}
.hero-copy{right:105px;top:172px;text-align:right}
.hero-copy .t1{font-size:20px;font-weight:300;color:#1d4e36}
.hero-copy .t2{font-size:14.5px;color:var(--green-dark);margin-top:10px}
.hero-copy .pt{font-size:17px;font-weight:500;color:#333;margin-top:8px;letter-spacing:-.3px}
.hero-copy .pt span{display:inline-block;width:4px;height:4px;background:#333;border-radius:50%;margin-left:7px;vertical-align:middle}
.dots{left:720px;top:366px;display:flex;gap:8px}
.dots i{width:10px;height:10px;border-radius:50%;background:#999}
.dots i:first-child{background:#555}

/* welcome */
.welcome-title{left:0;width:890px;top:428px;text-align:center;font-size:20px;font-weight:400;color:var(--green-dark)}
.welcome-text{left:85px;width:720px;top:463px;text-align:center;font-size:12.8px;font-weight:300;line-height:21.6px;color:#555}
.btn{top:558px;height:28px;font-size:10.5px;display:flex;align-items:center;justify-content:center;border-radius:2px}
.btn-outline{left:295px;width:83px;border:1px solid var(--green);color:var(--green-dark)}
.btn-dark{left:388px;width:207px;background:#3a3a3a;color:#fff}
.rule{left:74px;width:742px;height:1px;background:var(--line)}

/* vision */
.h2{font-size:21px;font-weight:400;color:var(--green-text)}
.vision-text{left:75px;top:674px;width:515px;font-size:11px;line-height:18.5px;color:#444}
.checks{left:77px;top:743px;width:500px;display:grid;grid-template-columns:248px 248px;row-gap:14.5px}
.checks li{list-style:none;font-size:13px;font-weight:500;letter-spacing:-.3px;color:var(--green-dark);display:flex;align-items:center;gap:8px;height:18px}
.arrows{left:795px;top:641px;display:flex;gap:6px}
.kids-cover{top:678px;height:146px;width:103px}

/* programs */
.view-all{left:548px;top:892px;font-size:10px;color:#555}
.program-card{left:77px;top:920px;width:505px;height:107px;background:var(--green);color:#fff;padding:12px 13px}
.program-card h3{font-size:12.5px;font-weight:400;margin-bottom:8px}
.program-card p{font-size:10px;line-height:18.3px;font-weight:300}
.program-card a{color:var(--gold);text-decoration:none}
.news-title{left:609px;top:883px;font-size:21px;font-weight:400;color:#222}
.news-box{left:610px;top:920px;width:206px;height:107px;background:var(--panel)}
.news-input{left:620px;top:938px;width:186px;height:30px;background:#fff;font-size:10px;color:#666;padding:9px 11px}
.news-submit{left:752px;top:979px;width:54px;height:25px;background:var(--submit);color:#fff;font-size:11px;font-weight:500;display:flex;align-items:center;justify-content:center;border:1px solid #8fdcb8}

/* partner band */
.band-top{left:77px;top:1046px;width:739px;height:5px;background:var(--yellow-band)}
.band-bottom{left:77px;top:1098px;width:739px;height:7px;background:var(--blue-band)}
.partner-name{left:80px;top:1063px;font-size:16px;font-weight:500;color:#222}
.partner-text{left:226px;top:1066px;width:565px;text-align:right;white-space:nowrap;font-size:12px;color:#666}
.partner-text a{color:var(--red);text-decoration:none;margin-left:4px}

/* footer */
.footer{left:0;top:1111px;width:890px;height:89px;background:var(--footer)}
.foot-links{left:74px;top:1136px;font-size:10px;color:#ccc;display:flex}
.foot-links span+span::before{content:"|";margin:0 7px;color:#999}
.copy{left:74px;top:1162px;font-size:10px;color:#ccc}
.social{left:692px;top:1143px;display:flex;gap:10px}
.social i{width:24px;height:24px;border-radius:50%}
</style>
</head>
<body>

<header>
  <div class="abs brand"><span class="brand-dot"></span>Maple Crest</div>
  <div class="abs call">Call us : <b>(555) 014-2290</b></div>
  <div class="abs search">Search
    <svg width="13" height="13" viewBox="0 0 13 13"><circle cx="5" cy="5" r="3.6" fill="none" stroke="#222" stroke-width="1.8"/><line x1="7.8" y1="7.8" x2="12" y2="12" stroke="#222" stroke-width="2.4"/></svg>
  </div>
</header>

<nav class="abs nav">
  <ul>
    <li class="active">HOME</li><li>PROGRAMS</li><li>MAPLE CREST</li><li>FEEPATH</li><li>EVENTS</li><li>KIDS PLACE</li><li>ABOUT US</li><li>MITESSORI</li><li>CONTACT</li>
  </ul>
</nav>

<section>
  <div class="abs hero-band"></div>
  <div class="abs hero-frame"></div>
  <div class="abs hero-photo" role="img" aria-label="Classroom of children raising hands toward a teacher at the chalkboard"></div>
  <div class="abs hero-copy">
    <div class="t1">MAPLE CREST</div>
    <div class="t2">MONTESSORI SCHOOLS - BROOKDALE</div>
    <div class="pt">SPORTS<span></span></div>
    <div class="pt">RECREATION<span></span></div>
    <div class="pt">HOMEWORK CLUB<span></span></div>
  </div>
  <div class="abs dots"><i></i><i></i><i></i><i></i></div>
</section>

<section>
  <h1 class="abs welcome-title">Welcome to Maple Crest</h1>
  <p class="abs welcome-text">The Maple Crest Before and After School Program exists to provide programming of the highest quality for your children, stressing a safe, secure environment; a nurturing, professional staff and lots of fun. We are committed to providing a fun-filled, rewarding program that supports the physical, mental, emotional and spiritual development of school-age children and their families to the fullest potential in order to improve their quality of life.</p>
  <div class="abs btn btn-outline">KNOW MORE</div>
  <div class="abs btn btn-dark">CHECK OUT OUR NEW BOOK SECTION</div>
  <div class="abs rule" style="top:613px"></div>
</section>

<section>
  <h2 class="abs h2" style="left:75px;top:635px">Our Vision</h2>
  <p class="abs vision-text">The BCR will be a leader in community programs for children and youth of all ages. We strive to be the best, the most innovative and cutting edge in the areas we serve. BCR will be a place where children and youth experience :</p>
  <ul class="abs checks">
    <li><svg width="10" height="8" viewBox="0 0 10 8"><path d="M1 4l3 3 5-6" fill="none" stroke="#1f5a3d" stroke-width="1.8"/></svg>POSITIVE REINFORCEMENT</li>
    <li><svg width="10" height="8" viewBox="0 0 10 8"><path d="M1 4l3 3 5-6" fill="none" stroke="#1f5a3d" stroke-width="1.8"/></svg>ACTIVITIES CONSEQUAT</li>
    <li><svg width="10" height="8" viewBox="0 0 10 8"><path d="M1 4l3 3 5-6" fill="none" stroke="#1f5a3d" stroke-width="1.8"/></svg>CHARACTER DEVLOPMENTS</li>
    <li><svg width="10" height="8" viewBox="0 0 10 8"><path d="M1 4l3 3 5-6" fill="none" stroke="#1f5a3d" stroke-width="1.8"/></svg>SOCIAL PROBLEM SOLVING</li>
    <li><svg width="10" height="8" viewBox="0 0 10 8"><path d="M1 4l3 3 5-6" fill="none" stroke="#1f5a3d" stroke-width="1.8"/></svg>ACCESS TO RESOURCES</li>
    <li><svg width="10" height="8" viewBox="0 0 10 8"><path d="M1 4l3 3 5-6" fill="none" stroke="#1f5a3d" stroke-width="1.8"/></svg>HEALTHY LIFESTYLES</li>
  </ul>

  <h2 class="abs h2" style="left:610px;top:635px">Kids Place</h2>
  <div class="abs arrows">
    <svg width="8" height="12" viewBox="0 0 8 12"><path d="M6 1L2 6l4 5" fill="none" stroke="#666" stroke-width="2"/></svg>
    <svg width="8" height="12" viewBox="0 0 8 12"><path d="M2 1l4 5-4 5" fill="none" stroke="#666" stroke-width="2"/></svg>
  </div>
  <div class="abs kids-cover" style="left:611px;background:linear-gradient(#5b6e1c,#7f9b2a 50%,#3e4a14)" role="img" aria-label="Children's film cover with a green fantasy scene"></div>
  <div class="abs kids-cover" style="left:714px;background:linear-gradient(#1b2448,#3b3a6a 60%,#7a5c6a)" role="img" aria-label="Children's film cover with a robot under a starry sky"></div>
  <div class="abs rule" style="top:860px"></div>
</section>

<section>
  <h2 class="abs h2" style="left:75px;top:883px">Programs</h2>
  <div class="abs view-all">View all</div>
  <div class="abs program-card">
    <h3>Maple Crest Before &amp; After School Program</h3>
    <p>Maple Crest at the BCR Community Rec Center provides before &amp; after school programming of the highest quality, stressing a safe, secure environment; a nurturing, professional team of staff; and lots of fun. We are committed to providing a fun-filled, rewarding program that balances... <a href="#">Know More</a></p>
  </div>
  <h2 class="abs news-title">Newsletter Signup</h2>
  <div class="abs news-box"></div>
  <div class="abs news-input">Enter your E-mail ID</div>
  <div class="abs news-submit">SUBMIT</div>
</section>

<section>
  <div class="abs band-top"></div>
  <div class="abs partner-name">FeePath</div>
  <div class="abs band-bottom"></div>
  <p class="abs partner-text">Mauris quis urna blandit, varius mi at, porttitor turpis dignissim id nisl fringilla dapibus.<a href="#">Know More</a></p>
</section>

<footer>
  <div class="abs footer"></div>
  <div class="abs foot-links"><span>Home</span><span>Programs</span><span>Maple Crest</span><span>FeePath</span><span>Events</span><span>Kids Place</span><span>About us</span><span>Mitessori</span><span>Contact</span></div>
  <div class="abs copy">Copyright ©&nbsp; 2013 &nbsp; MAPLE CREST. &nbsp; All rights reserved.</div>
  <div class="abs social"><i style="background:#3b5998"></i><i style="background:#2aa9e0"></i><i style="background:#1a7bb0"></i><i style="background:#f39200"></i></div>
</footer>

</body>
</html>
```